To design a brand identity that is simple and creative with 'Corvane' as the brand name, I like modern simple fonts like helvetica neue, I want to print both sides of the card, I am open to dark front and white back, but the design needs to transfer well to letter heads and email signatures, I am looking for sophisticated and elegant, but open minded about clever and off the wall, I do not do 'boring' Corvane Ventures is the mother company for a small group, specialising in Management & consulting, Software development and construction, we have a high level of integrity, we are transparent and accountable for what we do. my images are provided as a guide only, Im not expecting them to be just copied, Im looking for a creator and passionate thinker, who will put life into their work.

Target Market(s)

usually business minded people who are looking for something different in me, such as leadership, confidence and focus with thinking that is per haps a little outside the box..

Industry/Entity Type

Construction

Requirements
Must have
• clean, minmalistic
Nice to have
• custom logo
Should not have
• boring, traditional

```html
<!DOCTYPE html>
<html lang="en">
<head>
<meta charset="utf-8">
<title>Corvane business card</title>
<link rel="stylesheet" href="https://fonts.googleapis.com/css2?family=Open+Sans:ital,wght@0,300;0,400;0,600;0,700&family=Cormorant+Garamond:ital,wght@1,400&display=swap">
<style>
  :root {
    --backdrop: #e8e8ed;
    --card-dark: #2a2a2a;
    --card-dark-edge: #1c1c1c;
    --card-light: #ffffff;
    --orange: #f0642a;
    --white: #ffffff;
    --ink: #2f2f2f;
    --grey-text: #6f6f6f;
    --divider: #9a9a9a;
  }
  * { margin: 0; padding: 0; box-sizing: border-box; }
  html, body {
    width: 1200px; height: 987px; overflow: hidden;
    background: var(--backdrop);
    font-family: "Open Sans", Arial, sans-serif;
  }
  .stage {
    width: 1200px; height: 987px;
    display: flex; flex-direction: column; align-items: center; justify-content: center;
    gap: 44px;
  }
  .card {
    position: relative;
    width: 770px; height: 440px;
    border-radius: 26px;
    overflow: hidden;
    box-shadow: 0 10px 28px rgba(0,0,0,0.18);
  }
  /* Front */
  .card--front {
    background: linear-gradient(160deg, #353535 0%, var(--card-dark) 45%, var(--card-dark-edge) 100%);
    color: var(--white);
  }
  .brand-mark {
    position: absolute; left: 70px; top: 106px;
    display: flex; align-items: center; gap: 18px;
  }
  .brand-mark__dot {
    width: 40px; height: 40px; border-radius: 50%;
    background: var(--orange);
  }
  .brand-mark__name {
    font-size: 56px; font-weight: 400; color: var(--white); line-height: 1;
  }
  .divider {
    position: absolute; left: 418px; top: 60px;
    width: 2px; height: 150px;
    background: linear-gradient(to bottom, transparent, var(--divider), transparent);
  }
  .contact {
    position: absolute; left: 446px; top: 58px;
  }
  .contact__name { color: var(--orange); font-weight: 700; font-size: 27px; line-height: 1.1; }
  .contact__title { font-size: 19px; margin-bottom: 12px; }
  .contact__line {
    display: flex; align-items: center; gap: 10px;
    font-size: 18px; line-height: 1.6;
  }
  .contact__line svg { width: 18px; height: 18px; flex: none; }
  .services {
    position: absolute; left: 60px; bottom: 46px;
    color: var(--orange); font-size: 36px; font-weight: 400;
  }
  .services__sep { color: var(--white); font-size: 22px; vertical-align: middle; margin: 0 8px; }
  /* Back */
  .card--back { background: var(--card-light); }
  .lockup {
    position: absolute; left: 0; right: 0; top: 150px;
    display: flex; align-items: center; justify-content: center; gap: 24px;
  }
  .lockup__dot { width: 48px; height: 48px; border-radius: 50%; background: var(--orange); }
  .lockup__name {
    font-size: 80px; font-weight: 400; color: var(--ink); line-height: 1;
  }
  .tagline {
    position: absolute; left: 0; right: 0; top: 266px; text-align: center;
    font-family: "Cormorant Garamond", Georgia, serif; font-style: italic;
    font-size: 30px; color: var(--grey-text);
  }
</style>
</head>
<body>
<main class="stage">
  <section class="card card--front" aria-label="Card front">
    <div class="brand-mark">
      <span class="brand-mark__dot"></span>
      <span class="brand-mark__name">Corvane</span>
    </div>
    <div class="divider"></div>
    <div class="contact">
      <p class="contact__name">Your Name</p>
      <p class="contact__title">Title</p>
      <p class="contact__line">
        <svg viewBox="0 0 24 24" aria-hidden="true"><path fill="#f0642a" d="M6.6 10.8a15.1 15.1 0 0 0 6.6 6.6l2.2-2.2a1 1 0 0 1 1-.25 11.4 11.4 0 0 0 3.6.57 1 1 0 0 1 1 1V20a1 1 0 0 1-1 1A17 17 0 0 1 3 4a1 1 0 0 1 1-1h3.5a1 1 0 0 1 1 1c0 1.25.2 2.450.57 3.57a1 1 0 0 1-.25 1z"/></svg>
        +61 0400 517 264
      </p>
      <p class="contact__line">
        <svg viewBox="0 0 24 24" aria-hidden="true"><rect x="2" y="5" width="20" height="14" rx="2" fill="#f0642a"/><path d="M3 6l9 7 9-7" fill="none" stroke="#2a2a2a" stroke-width="1.8"/></svg>
        Names@corvane.ventures
      </p>
      <p class="contact__line">Po Box 418 Perth 6000</p>
    </div>
    <p class="services">Management<span class="services__sep">•</span>Software<span class="services__sep">•</span>Construction</p>
  </section>

  <section class="card card--back" aria-label="Card back">
    <div class="lockup">
      <span class="lockup__dot"></span>
      <span class="lockup__name">Corvane</span>
    </div>
    <p class="tagline">…in the creation business.</p>
  </section>
</main>
</body>
</html>
```